Business card for Luxury Portable Restroom Trailer company

We are a Luxury Portable Restroom Trailer Company Called FALCRIDGE HIRES. Based in Orange County California. We provide portable restroom trailers for events, such as, Weddings, Concerts, Charity events, Sporting events, Tournaments, Corporate events, ect. We rent and Sell the Luxury restrooms. Our colors are white, grey, and Orange. As you will see in the logo we uploaded.
There are 2 people in the company so the names and titles will change for the 3 people but card will remain the same. Here is the information for each Person: Dwight Penner CFO 555 318-0476
next Person: Leon Marchetti VP 555 318-0476
Next Person: Owen Marchetti CEO 555 318-0476
Information to include on the card: Luxury Restroom Trailers Rental and Sales. Weddings, Concerts, Charity, Sporting and Corp. Events.

```html
<!DOCTYPE html>
<html lang="en">
<head>
<meta charset="utf-8">
<title>FALCRIDGE HIRES — Business Card</title>
<link rel="stylesheet" href="https://fonts.googleapis.com/css2?family=Montserrat:wght@400;500;700;800&display=swap">
<style>
  :root {
    --backdrop: #e4e4e2;
    --card-dark: #2f3032;
    --card-mid: #3c3d40;
    --orange: #e0601f;
    --white: #f2f2f2;
    --grey-text: #d9d9d9;
  }
  * { box-sizing: border-box; margin: 0; padding: 0; }
  html, body { width: 1200px; height: 1200px; overflow: hidden; }
  body {
    background: var(--backdrop);
    font-family: "Montserrat", Arial, sans-serif;
    position: relative;
  }
  .card {
    position: absolute;
    left: 234px;
    width: 731px;
    height: 417px;
    background: linear-gradient(135deg, var(--card-dark) 0%, var(--card-mid) 100%);
    overflow: hidden;
  }
  .card--front { top: 160px; }
  .card--back { top: 632px; }

  .front-texture {
    position: absolute; inset: 0;
    background: radial-gradient(circle at 50% 45%, #424346 0%, #353638 60%, #2e2f31 100%);
  }
  .front-ring {
    position: absolute;
    left: 319px; top: 109px;
    width: 94px; height: 94px;
    border: 5px solid var(--orange);
    border-radius: 50%;
  }
  .front-name {
    position: absolute;
    left: 0; right: 0; top: 236px;
    text-align: center;
    font-weight: 800;
    font-size: 40px;
    letter-spacing: 1px;
    color: var(--orange);
  }

  .back-mark {
    position: absolute;
    left: 133px; top: 109px;
    width: 146px; height: 146px;
    border: 5px solid var(--orange);
    border-radius: 50%;
    display: flex; flex-direction: column;
    align-items: center; justify-content: center;
    font-weight: 800; font-size: 17px; line-height: 1.2;
    color: var(--orange); letter-spacing: 0.5px;
  }
  .divider {
    position: absolute;
    left: 309px; top: 107px;
    width: 2px; height: 149px;
    background: var(--grey-text);
  }
  .person {
    position: absolute;
    left: 342px; top: 105px;
  }
  .person-name {
    font-weight: 700; font-size: 30px; line-height: 34px;
    color: var(--orange);
  }
  .person-title {
    font-weight: 400; font-size: 19px; line-height: 22px;
    color: var(--white);
  }
  .contacts {
    list-style: none;
    margin-top: 18px;
  }
  .contacts li {
    display: flex; align-items: center;
    height: 27px;
    font-size: 19px; color: var(--white);
  }
  .contacts svg { width: 16px; height: 16px; margin-right: 10px; flex: none; }
  .tagline {
    position: absolute; left: 0; right: 0; top: 328px;
    text-align: center;
    font-weight: 700; font-size: 17.5px; color: var(--orange);
  }
  .services {
    position: absolute; left: 0; right: 0; top: 355px;
    text-align: center;
    font-size: 18.5px; color: var(--grey-text);
  }
  .services .sep { color: var(--orange); margin: 0 4px; }
</style>
</head>
<body>
  <section class="card card--front">
    <div class="front-texture" role="img" aria-label="Faint repeating brand-mark pattern in dark grey"></div>
    <div class="front-ring"></div>
    <div class="front-name">FALCRIDGE HIRES</div>
  </section>

  <section class="card card--back">
    <div class="back-mark"><span>FALCRIDGE</span><span>HIRES</span></div>
    <div class="divider"></div>
    <div class="person">
      <h1 class="person-name">Dwight Penner</h1>
      <p class="person-title">CFO</p>
      <ul class="contacts">
        <li>
          <svg viewBox="0 0 16 16" aria-hidden="true"><path fill="#e0601f" d="M3.5 1.5l2.2 2.6-1.3 1.6c.9 2 2.4 3.5 4.4 4.4l1.6-1.3 2.6 2.2-1.2 2.2c-5-.4-9.1-4.5-9.5-9.5z"/><path fill="none" stroke="#e0601f" stroke-width="1.2" d="M9 2.5a4.5 4.5 0 0 1 4.5 4.5M9 5a2 2 0 0 1 2 2"/></svg>
          555 318-0476
        </li>
        <li>
          <svg viewBox="0 0 16 16" aria-hidden="true"><rect x="1" y="3" width="14" height="10" fill="#e0601f"/><path d="M1.5 3.5L8 9l6.5-5.5" fill="none" stroke="#2f3032" stroke-width="1.3"/></svg>
          info@falcridgehires.com
        </li>
        <li>
          <svg viewBox="0 0 16 16" aria-hidden="true"><circle cx="8" cy="8" r="6.5" fill="none" stroke="#e0601f" stroke-width="1.6"/><ellipse cx="8" cy="8" rx="2.8" ry="6.5" fill="none" stroke="#e0601f" stroke-width="1.3"/><path d="M1.5 8h13" stroke="#e0601f" stroke-width="1.3"/></svg>
          www.falcridgehires.com
        </li>
      </ul>
    </div>
    <p class="tagline">Luxury Restroom Trailers Rental and Sales</p>
    <p class="services">Weddings<span class="sep">|</span>Concerts<span class="sep">|</span>Charity<span class="sep">|</span>Sporting<span class="sep">|</span>Corp. Events</p>
  </section>
</body>
</html>
```